Process Diagram - Circular Economy

I would like for a designer to take this rough sketch and turn it into a high quality design which can be used in a business presentation. Seeking to get both PDF and Jpeg file versions of the finished product.

Colours don't have to be the exact same as the rough sketch PDF, the green used is pretty ugly so open to some changes.

Target Market(s)

Corporate audience

Requirements
Must have
• Clear text for each party; VENOR, MORLAN, BUYER

Smaller text for the functions; marketing, recovery, logistics, cleaning, decontamination, testing & re-certification, storage, engineering suitability

```html
<!DOCTYPE html>
<html lang="en">
<head>
<meta charset="utf-8">
<title>Circular Economy Process Diagram</title>
<link href="https://fonts.googleapis.com/css2?family=Bebas+Neue&family=Oswald:wght@500;600&display=swap" rel="stylesheet">
<style>
  :root {
    --page: #ffffff;
    --callout: #2f64a0;
    --vendor-red: #e8383d;
    --band-orange: #f0883a;
    --ring-yellow: #fcc419;
    --ring-orange: #f59a3a;
    --arrow-yellow: #f7ec30;
    --arrow-green: #8dc63f;
    --marketing-purple: #6b3a7d;
    --hub-orange: #f05a28;
    --label-ink: #1a1a1a;
    --white: #ffffff;
  }
  html, body {
    margin: 0;
    padding: 0;
    width: 1200px;
    height: 1200px;
    overflow: hidden;
    background: var(--page);
  }
  .diagram { display: block; width: 1200px; height: 1200px; }
  .callout-box { fill: var(--callout); }
  .callout-text {
    font-family: "Bebas Neue", "Oswald", sans-serif;
    font-size: 27px;
    letter-spacing: 1.5px;
    fill: var(--white);
  }
  .party-name {
    font-family: "Bebas Neue", "Oswald", sans-serif;
    fill: var(--white);
    letter-spacing: 0.5px;
  }
  .party-name--vendor { font-size: 25px; }
  .party-name--buyer { font-size: 26px; }
  .party-name--hub { font-size: 13px; fill: var(--hub-orange); letter-spacing: 1px; }
  .band-label {
    font-family: "Oswald", sans-serif;
    font-weight: 500;
    font-size: 14px;
    letter-spacing: 1.5px;
    fill: var(--white);
  }
  .step-label {
    font-family: "Oswald", sans-serif;
    font-weight: 600;
    font-size: 8.5px;
    letter-spacing: 0.8px;
    fill: var(--label-ink);
  }
  .track-dash {
    fill: none;
    stroke: var(--white);
    stroke-width: 1.6;
    stroke-dasharray: 46 30;
  }
  .route-line { stroke: var(--white); stroke-width: 1.6; }
</style>
</head>
<body>
<svg class="diagram" viewBox="0 0 1000 1000" xmlns="http://www.w3.org/2000/svg" aria-label="Circular economy process: vendor, MORLAN loop, buyer">
  <defs>
    <linearGradient id="ring-fill" x1="0" y1="0" x2="1" y2="0">
      <stop offset="0" stop-color="var(--ring-yellow)"/>
      <stop offset="0.55" stop-color="#fbbc1c"/>
      <stop offset="1" stop-color="var(--ring-orange)"/>
    </linearGradient>
    <linearGradient id="arrow-fill" x1="470" y1="0" x2="820" y2="0" gradientUnits="userSpaceOnUse">
      <stop offset="0" stop-color="var(--arrow-yellow)"/>
      <stop offset="0.45" stop-color="#e3e83a"/>
      <stop offset="1" stop-color="var(--arrow-green)"/>
    </linearGradient>
    <linearGradient id="band-fill" x1="240" y1="0" x2="640" y2="0" gradientUnits="userSpaceOnUse">
      <stop offset="0" stop-color="var(--vendor-red)"/>
      <stop offset="1" stop-color="var(--band-orange)"/>
    </linearGradient>
    <linearGradient id="marketing-fill" x1="250" y1="0" x2="610" y2="0" gradientUnits="userSpaceOnUse">
      <stop offset="0" stop-color="var(--marketing-purple)"/>
      <stop offset="1" stop-color="#7a4a7a"/>
    </linearGradient>
  </defs>

  <!-- Callouts -->
  <g class="callout callout--start">
    <rect class="callout-box" x="181" y="279" width="135" height="38"/>
    <polygon class="callout-box" points="290,317 314,317 288,346"/>
    <text class="callout-text" x="248" y="307" text-anchor="middle">END OF LIFE</text>
  </g>
  <g class="callout callout--end">
    <rect class="callout-box" x="671" y="279" width="135" height="38"/>
    <polygon class="callout-box" points="675,317 700,317 700,346"/>
    <text class="callout-text" x="738" y="307" text-anchor="middle">NEW LIFE</text>
  </g>

  <!-- Circular loop -->
  <circle class="loop-ring" cx="501" cy="607" r="134" fill="none" stroke="url(#ring-fill)" stroke-width="64"/>

  <!-- Outbound arrow to buyer -->
  <path class="buyer-arrow" fill="url(#arrow-fill)"
        d="M430,474 L718,388 L714,352 L824,432 L730,472 L732,440 L470,520 Z"/>
  <line class="route-line" x1="576" y1="452" x2="680" y2="427"/>

  <!-- Vendor band -->
  <path class="vendor-band" fill="none" stroke="url(#band-fill)" stroke-width="60"
        d="M240,410 L460,460 C480,465 490,473 501,473 A134 134 0 0 1 605,690"/>
  <path class="marketing-band" fill="none" stroke="url(#marketing-fill)" stroke-width="20"
        d="M250,440 L460,488 C480,493 490,499 501,499 A108 108 0 0 1 603,640"/>

  <circle class="track-dash" cx="501" cy="607" r="146" transform="rotate(-70 501 607)"/>

  <!-- Band labels -->
  <text class="band-label" x="338" y="458" transform="rotate(13 338 458)" text-anchor="middle">MARKETING</text>
  <text class="party-name party-name--buyer" x="712" y="430" transform="rotate(-14 712 430)" text-anchor="middle">BUYER</text>

  <!-- Process steps -->
  <text class="step-label" x="508" y="468" transform="rotate(10 508 468)" text-anchor="middle">RECOVERY</text>
  <text class="step-label" x="615" y="531" text-anchor="middle">LOGISTICS</text>
  <text class="step-label" x="638" y="609" text-anchor="middle">CLEANING</text>
  <text class="step-label" x="506" y="745" text-anchor="middle">DECONTAMINATION</text>
  <text class="step-label" x="405" y="697" text-anchor="middle">TESTING &amp;</text>
  <text class="step-label" x="405" y="710" text-anchor="middle">CERTIFICATION</text>
  <text class="step-label" x="368" y="611" text-anchor="middle">STORAGE</text>
  <text class="step-label" x="390" y="531" text-anchor="middle">ENGINEERING</text>
  <text class="step-label" x="390" y="544" text-anchor="middle">SUITABILITY</text>

  <!-- Parties -->
  <g class="party party--vendor">
    <circle cx="241" cy="410" r="57" fill="var(--vendor-red)"/>
    <circle cx="241" cy="410" r="44" fill="none" stroke="var(--white)" stroke-width="2"/>
    <text class="party-name party-name--vendor" x="241" y="419" text-anchor="middle">VENDOR</text>
  </g>
  <g class="party party--hub">
    <circle cx="605" cy="690" r="33" fill="var(--hub-orange)"/>
    <circle cx="605" cy="690" r="28" fill="var(--white)"/>
    <text class="party-name party-name--hub" x="605" y="695" text-anchor="middle">MORLAN</text>
  </g>
</svg>
</body>
</html>
```